Classy, Elegant, Simple Business Card Design

Looking to have a classy, simple, and elegant design. Want a top notch designed business card. I really like the look of the new torvane credit card. I also like the design I attached. I am trying to reach 21-29 year old females for booking us for there wedding or event. We offer Disc Jockey Service, Photo Booth Rentals, and Uplighting .

Target Market(s)

21-28 year old females

Contact Information for Business Card

Has to have logo, website, email, and phone number

Font styles to use
Other font styles liked:
• open to font choice, modern, clean
Designer to choose
33a6d7
0791cd
0555a3
ffffff

Requirements
Must have
• Has to have logo, website, email, and phone number
Nice to have
• I really like the design of the new torvane credit card. I also included my logo and some designs I like
Should not have
• clutter or too much info

```html
<!DOCTYPE html>
<html lang="en">
<head>
<meta charset="utf-8">
<title>Quillharbor Events — Business Card</title>
<link href="https://fonts.googleapis.com/css2?family=Montserrat:wght@400;600&display=swap" rel="stylesheet">
<style>
  :root {
    --backdrop: #5b5b5d;
    --card: #1f2024;
    --card-edge: #2a2b30;
    --silver: #a4a6ab;
    --blue: #0791cd;
    --blue-deep: #0555a3;
    --white: #ffffff;
  }
  html, body {
    margin: 0;
    padding: 0;
    width: 799px;
    height: 1200px;
    overflow: hidden;
    background: var(--backdrop);
    font-family: "Montserrat", Arial, sans-serif;
  }
  .sheet {
    position: relative;
    width: 799px;
    height: 1200px;
  }
  .card {
    position: absolute;
    left: 80px;
    width: 639px;
    height: 365px;
    background: var(--card);
    border: 1px solid var(--card-edge);
    box-sizing: border-box;
  }
  .card--front { top: 120px; }
  .card--back { top: 715px; }

  .front-brand {
    position: absolute;
    inset: 0;
    display: flex;
    align-items: center;
    justify-content: center;
  }
  .wordmark {
    margin: 0;
    font-weight: 600;
    font-size: 38px;
    letter-spacing: 3px;
    text-transform: uppercase;
    white-space: nowrap;
  }
  .wordmark--silver { color: var(--silver); }
  .wordmark--blue {
    color: var(--blue);
    font-size: 22px;
    letter-spacing: 2px;
  }

  .back-brand {
    position: absolute;
    left: 40px;
    top: 160px;
  }
  .holder {
    position: absolute;
    right: 40px;
    top: 52px;
    text-align: right;
  }
  .holder__name {
    margin: 0;
    color: var(--blue);
    font-weight: 600;
    font-size: 21px;
  }
  .holder__role {
    margin: 4px 0 0;
    color: var(--white);
    font-weight: 400;
    font-size: 14px;
  }
  .contact {
    position: absolute;
    right: 40px;
    bottom: 48px;
    margin: 0;
    padding: 0;
    list-style: none;
  }
  .contact__item {
    display: flex;
    align-items: center;
    justify-content: flex-end;
    gap: 12px;
    color: var(--white);
    font-size: 15px;
    line-height: 26px;
  }
  .contact__icon {
    width: 14px;
    height: 14px;
    fill: none;
    stroke: var(--blue);
    stroke-width: 1.6;
  }
</style>
</head>
<body>
<main class="sheet">
  <section class="card card--front" aria-label="Card front">
    <div class="front-brand">
      <p class="wordmark wordmark--silver">Quillharbor Events</p>
    </div>
  </section>

  <section class="card card--back" aria-label="Card back">
    <div class="back-brand">
      <p class="wordmark wordmark--blue">Quillharbor Events</p>
    </div>

    <div class="holder">
      <p class="holder__name">Mara Ellison</p>
      <p class="holder__role">Founder &amp; CEO</p>
    </div>

    <ul class="contact">
      <li class="contact__item">
        <span>952 4170 3382</span>
        <svg class="contact__icon" viewBox="0 0 14 14" aria-hidden="true">
          <path d="M3 1.5 L5.5 4 L4.2 5.6 Q5.5 8.5 8.4 9.8 L10 8.5 L12.5 11 L11 12.5 Q5 12 1.5 3 Z"/>
        </svg>
      </li>
      <li class="contact__item">
        <span>mara@quillharbor.com</span>
        <svg class="contact__icon" viewBox="0 0 14 14" aria-hidden="true">
          <rect x="1" y="3" width="12" height="8"/>
          <path d="M1 3 L7 8 L13 3"/>
        </svg>
      </li>
      <li class="contact__item">
        <span>www.quillharbor.com</span>
        <svg class="contact__icon" viewBox="0 0 14 14" aria-hidden="true">
          <circle cx="7" cy="7" r="5.5"/>
          <ellipse cx="7" cy="7" rx="2.4" ry="5.5"/>
          <path d="M1.5 7 H12.5"/>
        </svg>
      </li>
    </ul>
  </section>
</main>
</body>
</html>
```